Fresh, modern, fun business card for pediatric dental practice

Need a business card for fresh, modern, fun pediatric dental practice

Clean look that matches our website's font and colors

We prefer the look of curved corners on business cards

Target Market(s)

parents (mothers) of young children, professionals, mid-high class

Industry/Entity Type

Dental

Contact Information for Business Card

Maplebrook Pediatric Dentistry
482 Quarry Lane
Suite 517
Hollowmere, PA 17601
717.555.0193
www.maplebrookkidsdental.example

Mei-Ran Tsai, DMD
Corinne Walbeck, DMD
(we are working on our email address, but we would like that on the card as well)

Font styles to use
Sans Serif

Requirements
Must have
• All info; we would also like to make cards for individual staff members
• colors from our website and color palatte, attatched
• use same font and design as website for branding
Nice to have
• clean, simple card that has a pop of color
• we would like to see a few designs with our tag line "where smiles get brighter"
• we are not sure if we want to have it on there or not
• we would like to see a few designs incorporating the ribbon graphic on our website where the word WELCOME is

```html
<!DOCTYPE html>
<html lang="en">
<head>
<meta charset="utf-8">
<title>Maplebrook Pediatric Dentistry — Business Card</title>
<link rel="stylesheet" href="https://fonts.googleapis.com/css2?family=Poppins:wght@400;600&family=Roboto:wght@400;500&display=swap">
<style>
  :root {
    --sun: #fdb719;
    --berry: #c02c9c;
    --ink: #333333;
    --paper: #ffffff;
    --backdrop: #ececea;
  }
  * { box-sizing: border-box; margin: 0; padding: 0; }
  html, body { width: 1200px; height: 930px; overflow: hidden; }
  body { background: var(--backdrop); position: relative; font-family: "Roboto", sans-serif; }

  .card {
    position: absolute;
    width: 680px;
    height: 388px;
    border-radius: 22px;
    overflow: hidden;
    box-shadow: 0 8px 24px rgba(0,0,0,0.15);
  }
  .card--front { left: 120px; top: 60px; background: var(--sun); }
  .card--back  { left: 400px; top: 480px; background: var(--paper); }

  .brand-name {
    font-family: "Poppins", sans-serif;
    font-weight: 600;
    line-height: 1.05;
  }
  .brand-name .tagline {
    display: block;
    font-weight: 400;
    letter-spacing: 1.5px;
  }
  .card--front .brand-name {
    position: absolute;
    left: 0; right: 0; top: 140px;
    text-align: center;
    color: var(--paper);
    font-size: 58px;
  }
  .card--front .tagline { font-size: 28px; margin-top: 4px; }

  .card--back .brand-name {
    position: absolute;
    left: 46px; top: 178px;
    color: var(--sun);
    font-size: 42px;
  }
  .card--back .tagline { font-size: 21px; margin-top: 4px; color: var(--berry); }

  .divider {
    position: absolute;
    left: 318px; top: 110px;
    width: 2px; height: 150px;
    background: var(--berry);
  }

  .contact {
    position: absolute;
    left: 340px; top: 80px;
    color: var(--ink);
    font-size: 14px;
    line-height: 19px;
  }
  .contact .person {
    font-weight: 500;
    color: var(--sun);
    font-size: 22px;
    letter-spacing: 0.5px;
    text-transform: uppercase;
    line-height: 26px;
  }
  .contact .credential { margin-bottom: 6px; }
  .contact .line { display: flex; align-items: center; gap: 7px; }
  .contact .line svg { width: 11px; height: 11px; flex: none; }

  .wave { position: absolute; left: 0; top: 0; width: 680px; height: 388px; }
</style>
</head>
<body>

  <section class="card card--front" aria-label="Card front">
    <p class="brand-name">Maplebrook<span class="tagline">pediatric dentistry</span></p>
  </section>

  <section class="card card--back" aria-label="Card back">
    <svg class="wave" viewBox="0 0 680 388" aria-hidden="true">
      <path d="M0 388 L0 382 C240 378 390 330 500 300 C590 276 640 276 680 276 L680 388 Z" fill="var(--sun)"/>
      <path d="M0 372 C240 368 390 320 500 290 C590 266 640 266 680 266" fill="none" stroke="var(--berry)" stroke-width="5"/>
    </svg>

    <p class="brand-name">Maplebrook<span class="tagline">pediatric dentistry</span></p>

    <div class="divider"></div>

    <div class="contact">
      <p class="person">Corinne Walbeck</p>
      <p class="credential">DMD</p>
      <p>482 Quarry Lane</p>
      <p>Suite 517 Hollowmere, PA 17601</p>
      <p class="line">
        <svg viewBox="0 0 12 12"><path d="M3 1 L5 3.5 L4 5 Q5 7 7 8 L8.5 7 L11 9 L9.5 11 Q2 10 1 2.5 Z" fill="var(--sun)"/></svg>
        717.555.0193
      </p>
      <p class="line">
        <svg viewBox="0 0 12 12"><rect x="1" y="2.5" width="10" height="7" fill="none" stroke="var(--sun)" stroke-width="1.3"/><path d="M1 2.5 L6 6.5 L11 2.5" fill="none" stroke="var(--sun)" stroke-width="1.3"/></svg>
        hello@maplebrookdental.example
      </p>
      <p class="line">
        <svg viewBox="0 0 12 12"><circle cx="6" cy="6" r="4.8" fill="none" stroke="var(--sun)" stroke-width="1.2"/><ellipse cx="6" cy="6" rx="2" ry="4.8" fill="none" stroke="var(--sun)" stroke-width="1"/><path d="M1.2 6 H10.8" stroke="var(--sun)" stroke-width="1"/></svg>
        www.maplebrookkidsdental.example
      </p>
    </div>
  </section>

</body>
</html>
```